Email Marketing Campaign Brief

We want to do an email marketing campaign around our consulting services. The attached documents provide back ground on our work but additional copy can be found below:

KV7lr is committed to helping you, the educator, make informed buying decisions based on local control and independent reviews through a simple, impartial and an effective approach.
In education, there exists a vast array of educational solutions – such as reading, science, language arts, and math curricula; school-wide reform programs; interventions; after-school programs; and new educational technologies. In the marketplace, providers could, and most do, claim to be able to improve educational outcomes and, in many cases, they all pretend to be supported by evidence. But a cursory review reveals that most evidence consists of poorly designed or advocacy-driven studies with some providers having such inadequate research as could only be described as case studies.

So the problem for State and local education officials is that they must sort through a myriad of such claims to decide which solutions merit consideration for their schools and classrooms. One US official stated the problem saying “many of these practitioners have seen interventions (solutions), introduced with great fanfare as being able to produce dramatic gains, come and go over the years, yielding little in the way of positive and lasting change – a perception confirmed by the flat achievement results over the past 30 years in the Federal Survey of Scholastic Attainment long-term trend”

KV7lr is a process by which we make you, the educator, the locus of control

OUR Approach:
With four simple, yet highly effective steps, KV7lr guides educators through an informed buying process that’s based on local control and review.

Step 1 — Research, Review, and Evaluation Criteria

Step 2 — Cost / Benefit Analysis

Step 3 — Education Survey & Culture Scan

Step 4 — Negotiation & Representation

Target Market(s)

Education

Industry/Entity Type

Marketing

Font styles to use
Sans Serif

Colors
f9b46a
f37122

Requirements
Must have
• HTML format that can be used in an Email Campaign
Nice to have
• Additional Copy in Word

```html
<!DOCTYPE html>
<html lang="en">
<head>
<meta charset="utf-8">
<title>KV7lr Email Campaign</title>
<link rel="stylesheet" href="https://fonts.googleapis.com/css2?family=Montserrat:ital,wght@0,300;0,400;0,700;0,800;1,800;1,900&family=Open+Sans:wght@400;600;700&display=swap">
<style>
  :root{
    --orange:#f37122;
    --peach:#f9b46a;
    --amber:#f9a11b;
    --red:#d9262b;
    --cyan:#1fb5e0;
    --teal:#4ee8c2;
    --green:#1f7e5c;
    --blue:#139bd9;
    --ink:#2b2b2b;
    --muted:#555;
    --page:#eceef1;
    --white:#ffffff;
  }
  *{box-sizing:border-box;margin:0;padding:0}
  html,body{width:1200px;height:810px;overflow:hidden}
  body{background:var(--page);font-family:"Open Sans",Arial,sans-serif;color:var(--ink)}
  .email{position:absolute;left:140px;top:12px;width:920px;height:786px;background:var(--white);box-shadow:0 2px 10px rgba(0,0,0,.12);overflow:hidden}

  /* header */
  .masthead{position:relative;height:54px;display:flex}
  .brand{position:relative;width:300px;background:var(--orange);display:flex;align-items:center;padding-left:46px;clip-path:polygon(0 0,100% 0,92% 100%,0 100%)}
  .brand-stripe{position:absolute;left:0;bottom:0;width:150px;height:8px;background:var(--teal)}
  .brand-name{font-family:"Montserrat",sans-serif;font-weight:400;font-size:30px;color:var(--white);letter-spacing:.5px}
  .nav{flex:1;display:flex;margin-left:-24px}
  .nav-tab{flex:1;display:flex;align-items:center;justify-content:center;font-family:"Montserrat",sans-serif;font-weight:800;font-style:italic;font-size:16px;color:var(--white);clip-path:polygon(8% 0,100% 0,92% 100%,0 100%);margin-right:-22px}
  .nav-tab.research{background:var(--amber)}
  .nav-tab.policy{background:var(--red)}
  .nav-tab.practice{background:var(--cyan);margin-right:0;clip-path:polygon(8% 0,100% 0,100% 100%,0 100%)}

  /* hero */
  .hero{position:relative;height:232px}
  .hero-photo{position:absolute;inset:0;background:linear-gradient(100deg,#6a8fb0 0%,#c9a27d 30%,#e7c15a 55%,#7a9cc2 78%,#2d5ea8 100%)}
  .hero-banner{position:absolute;left:120px;bottom:42px;background:rgba(24,92,170,.88);padding:8px 22px;transform:rotate(-3deg)}
  .hero-title{font-family:"Montserrat",sans-serif;font-weight:900;font-style:italic;font-size:30px;color:var(--white)}
  .hero-sub{position:absolute;left:170px;bottom:14px;font-family:"Montserrat",sans-serif;font-weight:800;font-style:italic;font-size:17px;color:var(--white);transform:rotate(-3deg);text-shadow:0 1px 3px rgba(0,0,0,.4)}

  /* intro copy */
  .intro{display:grid;grid-template-columns:1fr 1fr;gap:26px;padding:14px 30px 6px;font-size:9.6px;line-height:1.42;color:var(--muted)}
  .intro p+p{margin-top:5px}
  .intro strong{color:var(--orange);font-weight:700}

  .approach{padding:6px 30px 8px;text-align:center}
  .approach h2{font-family:"Montserrat",sans-serif;font-weight:800;font-style:italic;font-size:18px;color:var(--ink)}
  .approach p{font-size:10.5px;color:var(--muted);margin-top:3px;font-style:italic}

  /* steps */
  .steps{display:grid;grid-template-columns:repeat(4,1fr);gap:10px;padding:6px 20px 0}
  .step{position:relative;height:198px;padding:40px 14px 12px;color:var(--white);clip-path:polygon(0 10%,6% 6%,12% 9%,20% 4%,28% 8%,36% 3%,44% 7%,52% 2%,60% 7%,68% 4%,76% 8%,84% 3%,92% 7%,100% 4%,100% 100%,0 100%)}
  .step.research{background:var(--green)}
  .step.cost{background:var(--orange)}
  .step.survey{background:var(--blue)}
  .step.negotiation{background:var(--amber)}
  .step-number{position:absolute;top:14px;right:14px;width:30px;height:30px;border-radius:50%;background:var(--white);border:3px solid var(--red);color:var(--red);font-family:"Montserrat",sans-serif;font-weight:800;font-size:15px;display:flex;align-items:center;justify-content:center}
  .step-title{font-family:"Montserrat",sans-serif;font-weight:300;font-size:13px;line-height:1.2;text-transform:uppercase;padding-right:34px}
  .step-list{list-style:none;margin-top:8px;font-size:9.5px;line-height:1.35}
  .step-list li{position:relative;padding-left:11px;margin-bottom:3px}
  .step-list li::before{content:"";position:absolute;left:0;top:5px;width:5px;height:5px;border-radius:50%;background:var(--white)}
  .step-foot{position:absolute;left:14px;right:14px;bottom:12px;display:flex;align-items:center;gap:10px}
  .step-icon{width:20px;height:20px}
  .read-more{background:var(--white);color:var(--red);font-family:"Montserrat",sans-serif;font-weight:700;font-size:9px;padding:4px 10px;text-transform:uppercase}

  /* implementation */
  .implementation{padding:14px 30px 0;border-top:0}
  .implementation h3{font-family:"Montserrat",sans-serif;font-weight:900;font-style:italic;font-size:22px;color:var(--orange);text-transform:uppercase}
  .implementation .tagline{font-family:"Montserrat",sans-serif;font-weight:300;font-size:14px;margin-top:2px}
  .implementation .cta{font-size:11px;margin-top:4px;color:var(--muted)}
  .implementation .cta strong{color:var(--ink);font-style:italic}
  .rule{height:2px;background:var(--peach);margin-top:8px;width:420px}
</style>
</head>
<body>
<main class="email">
  <header class="masthead">
    <div class="brand">
      <span class="brand-name">KV7lr</span>
      <span class="brand-stripe"></span>
    </div>
    <nav class="nav">
      <span class="nav-tab research">Research</span>
      <span class="nav-tab policy">Policy</span>
      <span class="nav-tab practice">Practice</span>
    </nav>
  </header>

  <section class="hero">
    <div class="hero-photo" role="img" aria-label="Photo of smiling school children and a teacher gathered around a classroom table"></div>
    <div class="hero-banner"><span class="hero-title">We help you to build geniuses</span></div>
    <div class="hero-sub">Research, Teaching, Learning</div>
  </section>

  <section class="intro">
    <div>
      <p><strong>KV7lr</strong> is committed to helping you, the educator, make informed buying decisions based on local control and independent reviews through a simple, impartial and an effective approach.</p>
      <p>In education, there exists a vast array of educational solutions – such as reading, science, language arts, and math curricula; school-wide reform programs; interventions; after-school programs; and new educational technologies. In the marketplace, providers could, and most do, claim to be able to improve educational outcomes and, in many cases, they all pretend to be supported by evidence. But a cursory review reveals that most evidence consists of poorly designed or advocacy-driven studies.</p>
    </div>
    <div>
      <p>So the problem for State and local education officials is that they must sort through a myriad of such claims to decide which solutions merit consideration for their schools and classrooms. One US official stated the problem saying “many of these practitioners have seen interventions (solutions), introduced with great fanfare as being able to produce dramatic gains, come and go over the years, yielding little in the way of positive and lasting change – a perception confirmed by the flat achievement results over the past 30 years in the Federal Survey of Scholastic Attainment long-term trend”</p>
      <p><strong>KV7lr</strong> is a process by which we make you, the educator, the locus of control</p>
    </div>
  </section>

  <section class="approach">
    <h2>OUR Approach:</h2>
    <p>With four simple, yet highly effective steps, KV7lr guides educators through an informed buying process that’s based on local control and review.</p>
  </section>

  <section class="steps">
    <article class="step research">
      <span class="step-number">1</span>
      <h4 class="step-title">Research, Review and Evaluation Criteria</h4>
      <ul class="step-list">
        <li>Identify needs and goals</li>
        <li>Program reviews and alignment to need</li>
        <li>Independent evaluation and data informed decisions</li>
      </ul>
      <div class="step-foot">
        <svg class="step-icon" viewBox="0 0 20 20" fill="none" stroke="#fff" stroke-width="2"><circle cx="8" cy="8" r="5.5"/><line x1="12" y1="12" x2="18" y2="18"/></svg>
        <span class="read-more">Read more</span>
      </div>
    </article>
    <article class="step cost">
      <span class="step-number">2</span>
      <h4 class="step-title">Cost / Benefit Analysis</h4>
      <ul class="step-list">
        <li>Program cost by research and evaluation of programs</li>
        <li>Summary of cost data and alignment to identified needs</li>
      </ul>
      <div class="step-foot">
        <svg class="step-icon" viewBox="0 0 20 20" fill="none" stroke="#fff" stroke-width="1.8"><path d="M10 3a5 5 0 0 0-3 9v2h6v-2a5 5 0 0 0-3-9z"/><line x1="7.5" y1="17" x2="12.5" y2="17"/></svg>
        <span class="read-more">Read more</span>
      </div>
    </article>
    <article class="step survey">
      <span class="step-number">3</span>
      <h4 class="step-title">Education Survey and Culture Scan</h4>
      <ul class="step-list">
        <li>Direct observation and classroom data</li>
        <li>Culture scan to identify education best practices</li>
        <li>Match to strategic plan goals and objectives</li>
      </ul>
      <div class="step-foot">
        <svg class="step-icon" viewBox="0 0 20 20" fill="none" stroke="#fff" stroke-width="1.8"><circle cx="10" cy="10" r="3"/><path d="M10 2v3M10 15v3M2 10h3M15 10h3M4.3 4.3l2.1 2.1M13.6 13.6l2.1 2.1M4.3 15.7l2.1-2.1M13.6 6.4l2.1-2.1"/></svg>
        <span class="read-more">Read more</span>
      </div>
    </article>
    <article class="step negotiation">
      <span class="step-number">4</span>
      <h4 class="step-title">Negotiation and Representation</h4>
      <ul class="step-list">
        <li>Conduct provider reviews and presentations</li>
        <li>Representation for contract and pricing negotiations</li>
        <li>Support district in independent decision making process</li>
      </ul>
      <div class="step-foot">
        <svg class="step-icon" viewBox="0 0 20 20" fill="none" stroke="#fff" stroke-width="1.8"><rect x="4" y="4" width="12" height="8"/><path d="M2 15h16"/></svg>
        <span class="read-more">Read more</span>
      </div>
    </article>
  </section>

  <section class="implementation">
    <h3>Program Implementation</h3>
    <p class="tagline">Keep You Connected to School District Need and Stakeholder Input</p>
    <div class="rule"></div>
    <p class="cta">We help you make informed buying decisions. <strong>Contact us today for a no-cost consultation</strong></p>
  </section>
</main>
</body>
</html>
```